Card and board game developer website, small e-commerce site

We are designing a website for Leaping Otter Engine Works. I need a homepage and a typical inside page designed.
The website navigation will be:
Home (where we'll introduce the games and the website)
Our Games (drops open into the two games)
Griffins of Marrowvale
Tidebound
Order Now
About Us
Contact
The header of the website will include the logo, the navigation and a link to a facebook page. The header will also include a cart icon and a link to My Account.
Then on the homepage I suggest we include a row for each game:
Griffins of Marrowvale
This row will include a photo (or maybe a series of photos that animate into each other) and quick info about the game plus two buttons: Info and Photos (which will go to the detail page with the photo gallery), and Order Now (which will take you to the product for ordering).
Tidebound
Your footer will contain a copyright note, plus links to:
Terms and conditions
Shipping and returns
FAQ
Contact
Account login
NOTE: the logo is the orange mokey. I've uploaded a brief with more information. The current website that we are redesigning is here https://www.leapingotterengine.example/
Please send me any questions that you have.
Target Market(s)
People interested in fun card and board games at home.

```html
<!DOCTYPE html>
<html lang="en">
<head>
<meta charset="utf-8">
<title>Leaping Otter Engine Works</title>
<link href="https://fonts.googleapis.com/css2?family=Montserrat:wght@500;600;700&family=Lato:wght@400;700&display=swap" rel="stylesheet">
<style>
:root{
  --orange:#f0822a;
  --ink:#111111;
  --white:#ffffff;
  --footer-bg:#efefef;
  --line:#d6d6d6;
  --hero-a:#f1f1f3;
  --hero-b:#dcdde2;
}
*{box-sizing:border-box;margin:0;padding:0}
html,body{width:1200px;height:2628px;overflow:hidden}
body{position:relative;background:var(--white);font-family:'Lato',sans-serif;color:var(--ink)}
.abs{position:absolute}
.head-font{font-family:'Montserrat',sans-serif}

/* header */
.site-header{position:absolute;left:0;top:0;width:1200px;height:165px;background:var(--white);box-shadow:0 2px 6px rgba(0,0,0,.08);z-index:2}
.brand{position:absolute;left:114px;top:58px;display:flex;align-items:center;gap:12px;font-family:'Montserrat',sans-serif;font-weight:700;font-size:17px;color:var(--orange);width:290px;line-height:1.25}
.brand-dot{width:44px;height:44px;border-radius:50%;background:var(--orange);flex:none}
.account{position:absolute;left:922px;top:26px;font-family:'Montserrat',sans-serif;font-weight:600;font-size:15px}
.social-dot{position:absolute;left:1057px;top:20px;width:31px;height:31px;border-radius:50%;background:#3b5998}
.header-rule{position:absolute;left:436px;top:74px;width:653px;height:1px;background:var(--line)}
.main-nav a{position:absolute;top:109px;font-family:'Montserrat',sans-serif;font-weight:600;font-size:15px;color:var(--ink);text-decoration:none}
.btn{display:flex;align-items:center;justify-content:center;font-family:'Montserrat',sans-serif;font-weight:700;color:var(--white);background:var(--orange);border-radius:26px;text-decoration:none}
.btn-shadow{box-shadow:3px 3px 0 #1a1a1a}
.nav-order{position:absolute;left:946px;top:96px;width:140px;height:43px;font-size:14px}

/* hero */
.hero{position:absolute;left:0;top:165px;width:1200px;height:585px;background:linear-gradient(90deg,var(--hero-a),var(--hero-b))}
.hero-photo{position:absolute;left:460px;top:0;width:740px;height:585px;background:radial-gradient(ellipse at 60% 55%,#5f7d3e 0%,#4c6a3a 35%,#8a8a7a 60%,rgba(220,221,226,0) 78%)}
.hero-kicker{position:absolute;left:112px;top:160px;font-family:'Montserrat',sans-serif;font-weight:600;font-size:21px}
.hero-title{position:absolute;left:110px;top:203px;font-family:'Montserrat',sans-serif;font-weight:700;font-size:41px;line-height:1.6}
.hero-title span{display:block}
.hero-title .sub{font-size:34px}
.hero-cta{position:absolute;left:112px;top:344px;width:178px;height:52px;font-size:17px}

/* about */
.about-mark{position:absolute;left:585px;top:822px;width:30px;height:30px;border-radius:50%;background:var(--orange)}
.about-title{position:absolute;left:0;top:878px;width:1200px;text-align:center;font-family:'Montserrat',sans-serif;font-weight:700;font-size:32px}
.about-title em{font-style:normal;color:var(--orange)}
.about-copy{position:absolute;left:180px;top:938px;width:840px;text-align:center;font-size:15px;line-height:29.5px}
.about-copy p+p{margin-top:29px}
.about-copy a{color:var(--orange)}
.read-more{position:absolute;left:509px;top:1171px;width:179px;height:50px;font-size:17px}

/* game cards */
.game-card{position:absolute;top:1315px;width:467px;height:813px;border-radius:12px;color:var(--white);text-align:center}
.game-card.orange{left:113px;background:var(--orange)}
.game-card.dark{left:622px;background:#0a0a0a}
.card-mark{position:absolute;left:219px;top:45px;width:30px;height:30px;border-radius:50%;background:var(--white)}
.card-title{position:absolute;left:0;top:97px;width:100%;font-family:'Montserrat',sans-serif;font-weight:700;font-size:31px}
.card-media{position:absolute;left:23px;top:155px;width:421px;height:293px;border:3px solid var(--white);border-radius:14px}
.orange .card-media{background:linear-gradient(180deg,#23357a 0%,#b8442a 45%,#c77a3a 70%,#dfe3ea 100%)}
.dark .card-media{background:linear-gradient(135deg,#e9e9ec 0%,#5f7d3e 45%,#2c2c2c 70%,#d9d6c4 100%)}
.card-copy{position:absolute;left:16px;top:480px;width:435px;font-size:15.5px;line-height:29px}
.card-actions{position:absolute;left:0;top:729px;width:100%;display:flex;justify-content:center;gap:36px}
.pill{width:178px;height:50px;border-radius:26px;font-family:'Montserrat',sans-serif;font-weight:700;font-size:15px;display:flex;align-items:center;justify-content:center;text-decoration:none}
.pill.light{background:var(--white);color:var(--orange)}
.orange .pill.outline{border:2px solid var(--white);color:var(--white)}
.dark .pill.fill{background:var(--orange);border:2px solid var(--white);color:var(--white)}

/* footer */
.site-footer{position:absolute;left:0;top:2233px;width:1200px;height:395px;background:var(--footer-bg)}
.footer-brand{position:absolute;left:0;top:120px;width:1200px;display:flex;justify-content:center;align-items:center;gap:14px;font-family:'Montserrat',sans-serif;font-weight:700;font-size:22px;color:var(--orange)}
.footer-brand .brand-dot{width:50px;height:50px}
.footer-links a{position:absolute;top:278px;font-family:'Montserrat',sans-serif;font-weight:500;font-size:15.5px;color:var(--ink);text-decoration:none}
.copyright{position:absolute;left:0;top:336px;width:1200px;text-align:center;font-family:'Montserrat',sans-serif;font-weight:500;font-size:14px}
</style>
</head>
<body>

<header class="site-header">
  <div class="brand"><span class="brand-dot"></span><span>Leaping Otter Engine Works</span></div>
  <a class="account">MY ACCOUNT</a>
  <span class="social-dot" aria-label="Social page"></span>
  <div class="header-rule"></div>
  <nav class="main-nav">
    <a style="left:445px">HOME</a>
    <a style="left:548px">OUR GAMES</a>
    <a style="left:700px">ABOUT US</a>
    <a style="left:825px">CONTACT</a>
  </nav>
  <a class="btn btn-shadow nav-order">ORDER NOW</a>
</header>

<section class="hero">
  <div class="hero-photo" role="img" aria-label="Photo of the board game box, game board, drawstring bags, cards and gold coins"></div>
  <div class="hero-kicker">WELCOME TO</div>
  <h1 class="hero-title"><span>LEAPING OTTER</span><span class="sub">ENGINE WORKS</span></h1>
  <a class="btn btn-shadow hero-cta">GET STARTED</a>
</section>

<section>
  <div class="about-mark"></div>
  <h2 class="about-title">ABOUT <em>LEAPING OTTER</em> ENGINE WORKS</h2>
  <div class="about-copy">
    <p>They say do what you love...At Leaping Otter Engine Works we love to dream big dreams and bring those dreams to life. We create games to entertain and engage the people that play them; games that invite and inspire players to add a bit of themselves to each game, and how it is played.</p>
    <p><a>Come play with us.</a> Temporibus autem quibusdam et aut officiis debitis aut rerum necessitatibus saepe eveniet ut et voluptates repudiandae sint et molestiae non recusandae. Itaque earum rerum hic tenetur a sapiente delectus, ut aut reiciendis voluptatibus maiores alias consequatur aut perferendis doloribus asperiores repellat.</p>
  </div>
  <a class="btn btn-shadow read-more">READ MORE</a>
</section>

<article class="game-card orange">
  <div class="card-mark"></div>
  <h3 class="card-title">GRIFFINS OF MARROWVALE</h3>
  <div class="card-media" role="img" aria-label="Box cover art for Griffins of Marrowvale"></div>
  <p class="card-copy">Welcome to Griffins of Marrowvale, the first board game where every player is a GRIFFIN. Conquer territory and build your empire. Plunder castles and collect a huge hoard of gold. Rescue relatively attractive royalty or maybe eat them. Who knows? All we know is that everyone's a winner when the pizza's delivered!** 2 - 6 players Playtime approximately 1.5 hours. Game comes with 4 griffin packs. Additional griffin expansion packs coming soon.</p>
  <div class="card-actions"><a class="pill light">INFO &amp; PHOTOS</a><a class="pill outline">ORDER NOW</a></div>
</article>

<article class="game-card dark">
  <div class="card-mark"></div>
  <h3 class="card-title">TIDEBOUND</h3>
  <div class="card-media" role="img" aria-label="Photo of the game components laid out on a table"></div>
  <p class="card-copy">Welcome to Tidebound, a fast paced card game of strategy and chance. Play your element cards (Earth, Air, Fire,Water) and wild cards (Guardian, Balance, Evolution, Genesis) wisely and be the first player to discard Al of their cards and declare yourself the master of the elements.<br><br>Coming to Backerly soon.</p>
  <div class="card-actions"><a class="pill light">INFO &amp; PHOTOS</a><a class="pill fill">ORDER NOW</a></div>
</article>

<footer class="site-footer">
  <div class="footer-brand"><span class="brand-dot"></span><span>Leaping Otter Engine Works</span></div>
  <nav class="footer-links">
    <a style="left:136px">TERMS &amp; CONDITIONS</a>
    <a style="left:397px">SHIPPING &amp; RETURNS</a>
    <a style="left:656px">FAQ</a>
    <a style="left:768px">CONTACT</a>
    <a style="left:924px">ACCOUNT LOGIN</a>
  </nav>
  <p class="copyright">COPYRIGHTS@2024.LEAPING OTTER ENGINE WORKS.ALL RIGHTS RESERVED</p>
</footer>

</body>
</html>
```